House flipping business web site needed

pinecrestholdingsgroup.example.
I am a residential developer in Northern NJ and I am looking for a fresh new updated website. I have an intro video about my company being made now. I don't update it very often but I want an easy format that I can add update photos to on projects I have worked on or homes I renovate for sale.

Target Market(s)

investors into my projects so a portfolio , people looking to sell their homes to me.

Industry/Entity Type

Real Estate Development

Number of Pages Required

4 page

Font styles to use
Serif

Colors
33b8a4
39a9d7
cadf82

Requirements
Must have
• space for an intro video about my company
• a portfolio with pictures and information about each project
• Markets we serve- Morris County, NJ
• My logo- already created
• SEO
• Yes I would like this to function over all platforms. Phone, computer, all platforms.
• history and background page
• I am looking for a completed page that I can upload to the site that hosts my website
Nice to have
• I want something creative, easy to navigate. modern.

```html
<!DOCTYPE html>
<html lang="en">
<head>
<meta charset="utf-8">
<title>Pinecrest Holdings Group</title>
<link href="https://fonts.googleapis.com/css2?family=Ubuntu:wght@400;500&family=Open+Sans:wght@400;600&display=swap" rel="stylesheet">
<style>
:root{
  --teal:#33b8a4;
  --teal-dark:#2a9f8e;
  --blue:#39a9d7;
  --blue-deep:#2b93c4;
  --ink:#3b4248;
  --muted:#6b7278;
  --line:#e3e6e8;
  --footer:#0e1215;
  --white:#ffffff;
}
*{margin:0;padding:0;box-sizing:border-box}
html,body{width:742px;height:1200px;overflow:hidden;background:var(--white)}
body{position:relative;font-family:"Open Sans",sans-serif;color:var(--ink)}
.abs{position:absolute}

/* header */
.header-bg{left:0;top:0;width:742px;height:94px;background:linear-gradient(90deg,#fff 40%,#eef1ef 100%)}
.brand{left:61px;top:4px;width:70px;height:62px;background:#f2f4f4;display:flex;align-items:center;justify-content:center;text-align:center;font-family:"Ubuntu",sans-serif;font-size:8px;color:var(--blue-deep);line-height:1.2;padding:4px}
.help{left:524px;top:29px;display:flex;align-items:center;gap:7px}
.help-icon{width:24px;height:24px;border-radius:50%;background:var(--blue);display:flex;align-items:center;justify-content:center}
.help-label{font-size:6px;color:var(--muted);text-transform:uppercase}
.help-phone{font-family:"Ubuntu",sans-serif;font-size:13px;color:var(--ink)}

/* nav */
.nav{left:69px;top:74px;width:605px;height:38px;display:flex;background:linear-gradient(180deg,#44b4df,var(--blue-deep));z-index:2}
.nav a{flex:1;display:flex;align-items:center;justify-content:center;color:var(--white);font-size:8px;text-decoration:none;text-transform:uppercase}
.nav a.active{background:linear-gradient(180deg,#3cc2ad,var(--teal-dark));flex:0 0 121px}

/* hero */
.hero{left:0;top:94px;width:742px;height:287px;background:linear-gradient(180deg,#c8cfc9 0%,#8a8d80 45%,#5d5a4e 100%)}
.hero-caption{left:175px;top:270px;width:397px;height:52px;background:rgba(70,70,70,.55);color:var(--white);font-family:"Ubuntu",sans-serif;font-size:19px;display:flex;align-items:center;justify-content:center}
.dots{left:348px;top:356px;display:flex;gap:4px}
.dots span{width:8px;height:8px;border-radius:50%;border:1px solid #ddd}
.dots span.on{background:var(--teal);border-color:var(--teal)}

/* welcome */
.welcome-title{left:68px;top:451px;font-family:"Ubuntu",sans-serif;font-size:13.5px;color:var(--ink);text-transform:uppercase}
.welcome-text{left:68px;top:478px;width:344px;font-size:6.4px;line-height:16px;color:var(--muted)}
.video{left:430px;top:441px;width:244px;height:147px;border:1px solid var(--line);padding:4px;background:var(--white)}
.video-frame{position:relative;width:100%;height:100%;background:linear-gradient(180deg,#7fa2c8 0%,#b9c3cc 45%,#6b6960 100%)}
.play{position:absolute;left:97px;top:38px;width:40px;height:40px;border-radius:50%;background:rgba(20,40,50,.75);display:flex;align-items:center;justify-content:center}
.progress{position:absolute;left:16px;top:114px;width:206px;height:8px;border-radius:4px;background:#1d2a30}
.progress i{display:block;width:80px;height:8px;border-radius:4px;background:var(--teal)}

/* portfolio */
.portfolio{left:0;top:634px;width:742px;height:374px;background:linear-gradient(180deg,#3aa6d0,#2f9cc6)}
.portfolio-title{left:0;top:701px;width:742px;text-align:center;font-family:"Ubuntu",sans-serif;font-size:12.5px;color:var(--white);text-transform:uppercase}
.card{top:751px;width:191px;height:113px;border:2px solid var(--white);background:#8c9193}
.card .photo{width:100%;height:77px}
.card .tag{height:32px;background:rgba(51,184,164,.92);color:var(--white);font-size:6.6px;display:flex;align-items:center;gap:4px;padding-left:12px}
.card-title{top:878px;width:191px;font-size:7.6px;font-weight:600;color:var(--white);padding-bottom:9px;border-bottom:1px solid rgba(255,255,255,.3)}
.card-text{top:914px;width:191px;font-size:6.2px;line-height:16px;color:#eaf6fb;text-align:justify}

/* info */
.info-title{top:1032px;font-family:"Ubuntu",sans-serif;font-size:13px;color:var(--ink);text-transform:uppercase}
.info-text{font-size:6.3px;line-height:16px;color:var(--muted)}
.contact-row{left:240px;display:flex;align-items:center;gap:8px}
.ring{width:24px;height:24px;border-radius:50%;border:1px solid #e0407a;display:flex;align-items:center;justify-content:center}
.contact-divider{left:240px;top:1076px;width:139px;height:1px;background:var(--line)}
.email{left:435px;top:1087px;width:143px;height:24px;border:1px solid #d4d8da;border-radius:2px;font-size:6.2px;color:#9aa0a5;display:flex;align-items:center;padding-left:10px}
.subscribe{left:586px;top:1087px;width:70px;height:24px;border-radius:2px;background:var(--teal);color:var(--white);font-size:7px;display:flex;align-items:center;justify-content:center;gap:4px;text-transform:uppercase}

/* footer */
.footer{left:0;top:1138px;width:742px;height:62px;background:var(--footer)}
.copyright{left:68px;top:1163px;font-size:6.4px;color:var(--white)}
.socials{left:583px;top:1158px;display:flex;gap:4px}
.socials span{width:20px;height:20px;border-radius:50%;border:1px solid #cfd3d6}
.socials span.on{background:var(--teal);border-color:var(--teal)}
</style>
</head>
<body>

<div class="abs header-bg"></div>
<div class="abs brand">Pinecrest Holdings Group</div>
<div class="abs help">
  <div class="help-icon"><svg width="12" height="12" viewBox="0 0 24 24"><path fill="#fff" d="M6.6 10.8a15 15 0 0 0 6.6 6.6l2.2-2.2c.3-.3.7-.4 1-.2 1.1.4 2.3.6 3.6.6.6 0 1 .4 1 1V20c0 .6-.4 1-1 1A17 17 0 0 1 3 4c0-.6.4-1 1-1h3.5c.6 0 1 .4 1 1 0 1.3.2 2.5.6 3.6.1.3 0 .7-.2 1z"/></svg></div>
  <div><div class="help-label">Need help?</div><div class="help-phone">555-014-PINE (7463)</div></div>
</div>

<nav class="abs nav">
  <a class="active" href="#">Home</a>
  <a href="#">About us</a>
  <a href="#">Services</a>
  <a href="#">Portfolio</a>
  <a href="#">Contact</a>
</nav>

<div class="abs hero" role="img" aria-label="Photo of a renovated two-storey sided house among trees"></div>
<div class="abs hero-caption">Markets we serve &nbsp;- Morris County, NJ</div>
<div class="abs dots"><span></span><span></span><span class="on"></span><span></span></div>

<h1 class="abs welcome-title">Welcome to &nbsp;Pinecrest Holdings Group</h1>
<div class="abs welcome-text">
  <p>Pinecrest Holdings Group is a family run business with 3rd generation builders and renovators in the Morris County area. As the President and owner of Pinecrest Holdings Group I am dedicated to working hard to create opportunities for investment through real estate.</p>
  <p>At Pinecrest Holdings Group we have a valuable support system and a team of investors, realtors, attorneys, contractors and property managers providing a combined package offering years of experience in the local market.</p>
</div>
<div class="abs video">
  <div class="video-frame" role="img" aria-label="Intro video still of a house under construction">
    <div class="play"><svg width="14" height="14" viewBox="0 0 14 14"><path d="M3 1l10 6-10 6z" fill="var(--teal)"/></svg></div>
    <div class="progress"><i></i></div>
  </div>
</div>

<section class="abs portfolio" role="img" aria-label="Faint blue-tinted photo of a wooded yard"></section>
<h2 class="abs portfolio-title">Our Portfolio</h2>

<div class="abs card" style="left:69px">
  <div class="photo" role="img" aria-label="Photo of a large renovated family house" style="background:linear-gradient(180deg,#c9cdd0,#8e8b7f)"></div>
  <div class="tag"><svg width="6" height="8" viewBox="0 0 12 16"><path fill="#fff" d="M6 0a6 6 0 0 0-6 6c0 4.5 6 10 6 10s6-5.5 6-10a6 6 0 0 0-6-6zm0 8.5A2.5 2.5 0 1 1 6 3.5a2.5 2.5 0 0 1 0 5z"/></svg>1Cras vel sapien in ex posuere</div>
</div>
<div class="abs card" style="left:276px">
  <div class="photo" role="img" aria-label="Photo of a small cottage on a wooded hillside" style="background:linear-gradient(180deg,#a99c8c,#6f6a60)"></div>
  <div class="tag"><svg width="6" height="8" viewBox="0 0 12 16"><path fill="#fff" d="M6 0a6 6 0 0 0-6 6c0 4.5 6 10 6 10s6-5.5 6-10a6 6 0 0 0-6-6zm0 8.5A2.5 2.5 0 1 1 6 3.5a2.5 2.5 0 0 1 0 5z"/></svg>45,Cras vel sapien in ex posuere</div>
</div>
<div class="abs card" style="left:482px">
  <div class="photo" role="img" aria-label="Photo of a house frame under construction" style="background:linear-gradient(180deg,#b8b2a8,#7a6a58)"></div>
  <div class="tag"><svg width="6" height="8" viewBox="0 0 12 16"><path fill="#fff" d="M6 0a6 6 0 0 0-6 6c0 4.5 6 10 6 10s6-5.5 6-10a6 6 0 0 0-6-6zm0 8.5A2.5 2.5 0 1 1 6 3.5a2.5 2.5 0 0 1 0 5z"/></svg>37,Cras vel sapien in ex posuere</div>
</div>

<h3 class="abs card-title" style="left:69px">Lorem ipsum dolor sit amet, consectetur</h3>
<h3 class="abs card-title" style="left:276px">Lorem ipsum dolor sit amet, consectetur</h3>
<h3 class="abs card-title" style="left:482px">Lorem ipsum dolor sit amet, consectetur</h3>
<p class="abs card-text" style="left:69px">Maecenas sed faucibus enim. Nullam a tincidunt lacus. Praesent lobortis id nisi vitae accumsan.</p>
<p class="abs card-text" style="left:276px">Maecenas sed faucibus enim. Nullam a tincidunt lacus. Praesent lobortis id nisi vitae accumsan.</p>
<p class="abs card-text" style="left:482px">Maecenas sed faucibus enim. Nullam a tincidunt lacus. Praesent lobortis id nisi vitae accumsan.</p>

<h2 class="abs info-title" style="left:68px">About us</h2>
<p class="abs info-text" style="left:68px;top:1052px;width:150px">We are a team of experienced home buyers and renovators in the Morris County, NJ area. Our specialty is purchasing distressed homes and property.</p>

<div class="abs contact-row" style="top:1043px">
  <div class="ring"><svg width="10" height="10" viewBox="0 0 24 24"><path fill="#e0407a" d="M6.6 10.8a15 15 0 0 0 6.6 6.6l2.2-2.2c.3-.3.7-.4 1-.2 1.1.4 2.3.6 3.6.6.6 0 1 .4 1 1V20c0 .6-.4 1-1 1A17 17 0 0 1 3 4c0-.6.4-1 1-1h3.5c.6 0 1 .4 1 1 0 1.3.2 2.5.6 3.6.1.3 0 .7-.2 1z"/></svg></div>
  <span style="font-family:'Ubuntu',sans-serif;font-size:9.5px;color:var(--ink)">555-014-PINE (7463)</span>
</div>
<div class="abs contact-divider"></div>
<div class="abs contact-row" style="top:1085px">
  <div class="ring"><svg width="8" height="10" viewBox="0 0 12 16"><path fill="#e0407a" d="M6 0a6 6 0 0 0-6 6c0 4.5 6 10 6 10s6-5.5 6-10a6 6 0 0 0-6-6zm0 8.5A2.5 2.5 0 1 1 6 3.5a2.5 2.5 0 0 1 0 5z"/></svg></div>
  <span style="font-family:'Ubuntu',sans-serif;font-size:7.2px;line-height:13px;color:var(--muted)">Morris County,<br>NJ |</span>
</div>

<h2 class="abs info-title" style="left:435px">Newsletter signup</h2>
<p class="abs info-text" style="left:435px;top:1051px;width:215px;line-height:13px">We only work in the Morris County area so we are local and know the area and market. We can finance or buy your home for cash.</p>
<div class="abs email">Email Address</div>
<div class="abs subscribe"><svg width="8" height="6" viewBox="0 0 16 12"><path fill="#fff" d="M0 0h16v12H0z"/><path d="M0 0l8 6 8-6" stroke="var(--teal)" stroke-width="1.5" fill="none"/></svg>Subscribe</div>

<footer class="abs footer"></footer>
<p class="abs copyright">Copyrights@2016 Pinecrest Holdings Group. All Right Reserved.</p>
<div class="abs socials" aria-label="Social links"><span></span><span class="on"></span><span></span><span></span></div>

</body>
</html>
```